Computer Training in the Education sector - Letterhead

We need a new letter head to be designed for the company. We provide computer training fro the Education Sector, both primary and private tertiary providers. The colours will need to tie in with the website www.crossingthestream.co.nz.
The company name is Crossing the Stream with the tag line of Computer Training for Educators.
The footer will need to have the following detail...
0508 PCS MENTOR
021 839 415
www.crossingthestream.co.nz / training@crossingthestream.co.nz
Updates

Thanks for the designs so far.

Some have watermarks in the background. Please don't worry about using watermarks as I will not be using a watermark in in a final design.
Regards,
Roger

Thank you for all the designs and the effort. There was some great concepts that came through.

Cheers
Roger

Industry/Entity Type

Computer

```html
<!DOCTYPE html>
<html lang="en">
<head>
<meta charset="utf-8">
<title>Crossing the Stream – Letterhead</title>
<link href="https://fonts.googleapis.com/css2?family=Arimo:wght@400;700&display=swap" rel="stylesheet">
<style>
  :root {
    --paper: #ffffff;
    --ink: #1d1d1d;
    --brand-blue: #2f7fc1;
    --brand-green: #86bc3c;
    --brand-orange: #e8832f;
    --faint-blue: #e9f1f9;
    --faint-orange: #fcefe5;
    --rule: #8a8a8a;
  }
  * { margin: 0; padding: 0; box-sizing: border-box; }
  html, body {
    width: 1034px;
    height: 1200px;
    overflow: hidden;
    background: var(--paper);
  }
  .letterhead {
    position: relative;
    width: 1034px;
    height: 1200px;
    background: var(--paper);
    font-family: "Arimo", Arial, sans-serif;
    color: var(--ink);
  }
  .brand {
    position: absolute;
    left: 62px;
    top: 40px;
    width: 160px;
    display: flex;
    align-items: center;
    gap: 10px;
  }
  .brand-dot {
    flex: 0 0 18px;
    height: 18px;
    border-radius: 50%;
    background: var(--brand-green);
  }
  .brand-name {
    font-size: 26px;
    font-weight: 700;
    line-height: 1.1;
    color: var(--brand-blue);
  }
  .tagline {
    position: absolute;
    left: 235px;
    top: 92px;
    font-size: 18px;
    font-weight: 700;
    letter-spacing: 1.6px;
  }
  .backdrop-mark {
    position: absolute;
    left: 380px;
    top: 720px;
    width: 470px;
    height: 460px;
    display: flex;
    align-items: center;
    justify-content: center;
    border-radius: 50%;
    border: 26px solid var(--faint-orange);
  }
  .backdrop-name {
    font-size: 78px;
    font-weight: 400;
    line-height: 1;
    text-align: center;
    color: var(--faint-blue);
  }
  .contact {
    position: absolute;
    left: 60px;
    top: 1082px;
    padding-left: 11px;
    border-left: 1px solid var(--rule);
    list-style: none;
    font-size: 15px;
    line-height: 24.5px;
  }
</style>
</head>
<body>
  <main class="letterhead">
    <header>
      <div class="brand">
        <span class="brand-dot"></span>
        <span class="brand-name">Crossing the Stream</span>
      </div>
      <p class="tagline">Computer Training for Educators</p>
    </header>

    <div class="backdrop-mark" aria-hidden="true">
      <span class="backdrop-name">Crossing<br>the Stream</span>
    </div>

    <footer>
      <ul class="contact">
        <li>P: 0508 PCS MENTOR</li>
        <li>F: 021 839 415</li>
        <li>E: training@crossingthestream.co.nz</li>
        <li>W: www.crossingthestream.co.nz</li>
      </ul>
    </footer>
  </main>
</body>
</html>
```